Modernize Website: marcusfellwright.net

I am a novelist with an older-generation website at: marcusfellwright.net.

I am hoping to refresh this outdated website with a new, responsive redesign. I would prefer to host the code myself, and edit using Adobe Dreamweaver. So I’m not looking to use a hosted site builder like Plexo. Nor am I looking to use a CMS like Pagecraft.

In order to simplify the old site, there are a number of sections I’ll be looking to remove during this redesign. These are shown in the "MF Site Redesign" attachment. I can also provide imagery for new content (another book series in addition to the existing one), as well as higher-resolution imagery (if needed) of the old content.

Happy to answer any further questions.
Updates

I've uploaded a ZIP file containing high-res artwork associated with the new trilogy of books.

Target Market(s)

Readers of epic fantasy novels such as H.W.B. Castellane's THE WARDEN OF THE VALES, Harold P.Q. Ventris's A CROWN OF ASH AND RAIN, Victor Halloway's THE GATE OF STARS, or Dennis Vale's BLADE OF MERIVANE.

Industry/Entity Type

Entertainment

Coding

Coded - Design and coding required

Number of Pages Required

5+ page

Font styles to use
Serif
Decorative

Colors

Designer to choose colors to be used in the design.

Requirements
Must have
• I'm looking for a responsive design that displays nicely on both mobile and desktop devices. Existing site contains multiple pages, but these can obviously be combined into fewer pages (or even one) by divisions such as tabs, sections, and/or modal windows. See marcusfellwright.net for current content and "MF Site Redesign" attachment for content to be removed at this time.
Nice to have
• The ability to fulfill orders of autographed books directly from the website. I currently use Coinlo to do this, but it would be nice to incorporate a more comprehensive merchant service at a reasonable rate.
Should not have
• I'd like to host and control the site code myself. So please don't use a hosted web builder like Plexo, or a cloud-based CMS like Pagecraft.

```html
<!DOCTYPE html>
<html lang="en">
<head>
<meta charset="utf-8">
<title>Marcus Fellwright — The Legend of Varneth</title>
<link href="https://fonts.googleapis.com/css2?family=Cinzel:wght@400;700&family=Open+Sans:wght@400;600;700&display=swap" rel="stylesheet">
<style>
:root{
  --ink:#0c0a0a;
  --red:#c1121f;
  --white:#ffffff;
  --text-soft:#e8e2e0;
  --line:#6b6464;
  --serif:'Cinzel', Georgia, serif;
  --sans:'Open Sans', Arial, sans-serif;
}
*{box-sizing:border-box;margin:0;padding:0}
html,body{width:1200px;height:2594px;overflow:hidden;background:var(--ink)}
body{font-family:var(--sans);color:var(--white)}
.page{position:relative;width:1200px;height:2594px;overflow:hidden}
.abs{position:absolute}

/* hero */
.hero{left:0;top:0;width:1200px;height:560px}
.hero-art{left:0;top:0;width:1200px;height:560px;
  background:
    radial-gradient(ellipse 300px 200px at 27% 70%,rgba(255,150,50,.85) 0%,rgba(210,80,20,.6) 35%,transparent 75%),
    radial-gradient(ellipse 420px 330px at 22% 50%,rgba(120,45,20,.9) 0%,rgba(70,30,20,.6) 50%,transparent 85%),
    radial-gradient(ellipse 260px 230px at 78% 42%,rgba(120,120,118,.55) 0%,transparent 80%),
    radial-gradient(ellipse 380px 140px at 6% 78%,rgba(200,110,50,.45) 0%,transparent 80%),
    linear-gradient(180deg,#4a4e52 0%,#34373a 30%,#2a2826 60%,#1d1411 85%,#120c0a 100%)}
.hero-shade{left:0;top:0;width:1200px;height:560px;background:linear-gradient(90deg,rgba(0,0,0,0) 40%,rgba(0,0,0,.25) 100%)}
.brand{left:97px;top:18px;font-family:var(--serif);font-size:30px;line-height:30px;color:#e9e4dc;letter-spacing:1px}
.nav{left:0;top:34px;font-size:15px;font-weight:600}
.nav a{position:absolute;color:var(--white);text-decoration:none;white-space:nowrap}
.caret{display:inline-block;width:0;height:0;border-left:5px solid transparent;border-right:5px solid transparent;border-top:6px solid var(--white);margin-left:4px;vertical-align:middle}
.search{left:980px;top:33px;width:120px;height:32px;border:1.5px solid var(--white);font-size:13px;display:flex;align-items:center;padding-left:20px;gap:18px}
.hero-title{left:558px;top:214px;font-family:var(--serif);font-weight:700;font-size:62px;line-height:72px;color:var(--white);text-shadow:0 2px 8px rgba(0,0,0,.6)}

/* novels */
.novels{left:0;top:560px;width:1200px;height:538px;background:radial-gradient(ellipse 700px 320px at 50% 55%,#1b1717,transparent 80%),linear-gradient(180deg,#0a0909,#141111 60%,#0b0a0a)}
.section-title{font-family:var(--serif);font-weight:700;font-size:36px;color:var(--white)}
.novels .section-title{left:0;width:1200px;text-align:center;top:72px}
.cover{top:159px;width:208px;height:306px;border:1.5px solid #bdb6b0;box-shadow:0 6px 18px rgba(0,0,0,.7)}
.cover-1{left:218px;background:radial-gradient(ellipse 90px 70px at 50% 55%,rgba(220,80,110,.55),transparent 80%),linear-gradient(180deg,#b7b3bd 0%,#8d8797 22%,#6a5563 50%,#3f2e3a 80%,#241b24 100%)}
.cover-2{left:496px;background:radial-gradient(ellipse 110px 90px at 45% 62%,rgba(255,190,80,.7),transparent 80%),linear-gradient(180deg,#e06a2a 0%,#c2471d 30%,#8c2c14 65%,#3e1309 100%)}
.cover-3{left:775px;background:radial-gradient(ellipse 100px 80px at 50% 72%,rgba(240,140,50,.65),transparent 80%),linear-gradient(180deg,#9fb0ba 0%,#6d7f8a 28%,#6a4a38 60%,#3a1f16 100%)}
.arrow{width:26px;height:30px}

/* world */
.world{left:0;top:1098px;width:1200px;height:365px;background:
  radial-gradient(ellipse 520px 260px at 40% 45%,rgba(140,80,30,.75),transparent 80%),
  radial-gradient(ellipse 300px 200px at 88% 70%,rgba(110,60,25,.55),transparent 80%),
  linear-gradient(180deg,#2c1a10 0%,#4a2a14 50%,#24140c 100%)}
.feature{width:124px;height:124px;border:3.5px solid var(--white);border-radius:50%;display:flex;align-items:center;justify-content:center;top:90px}
.feature-label{top:228px;width:180px;text-align:center;font-size:19px;font-weight:600}
.world .section-title{left:832px;top:78px}
.world-text{left:833px;top:138px;font-size:19px;font-weight:600;line-height:31px}
.world-text em{font-style:italic}
.btn-outline{left:833px;top:228px;width:204px;height:50px;border:1.5px solid var(--white);font-size:19px;font-weight:700;display:flex;align-items:center;justify-content:center}

/* author */
.author{left:0;top:1463px;width:1200px;height:496px;background:
  radial-gradient(ellipse 380px 300px at 25% 45%,rgba(70,55,55,.6),transparent 80%),
  radial-gradient(ellipse 500px 300px at 75% 30%,rgba(45,38,38,.6),transparent 80%),
  linear-gradient(180deg,#1e1a1a,#141111 60%,#100d0d)}
.portrait{left:104px;top:69px;width:352px;height:352px;border-radius:50%;border:2px solid #9b1b22;overflow:hidden;
  background:
    radial-gradient(ellipse 120px 70px at 55% 30%,rgba(30,22,22,.9),transparent 80%),
    linear-gradient(180deg,transparent 58%,#151011 70%,#0c0909 100%),
    radial-gradient(circle at 28% 40%,#a07a78,#7e5a5c 40%,#4a3234 75%,#2a1c1e)}
.author .section-title{left:553px;top:72px}
.bio{left:557px;top:128px;width:548px;font-size:11.6px;letter-spacing:-.1px;line-height:23px;color:var(--text-soft)}
.bio p+p{margin-top:10px}
.btn-red{left:557px;top:373px;width:110px;height:37px;background:var(--red);font-size:15px;font-weight:700;display:flex;align-items:center;justify-content:center}

/* testimonial */
.quote-band{left:0;top:1959px;width:1200px;height:294px;background:linear-gradient(100deg,#1e0507 0%,#4a080b 45%,#a61a1e 100%)}
.quote-badge{left:550px;top:-24px;width:100px;height:100px;border-radius:50%;background:#0d0909;display:flex;align-items:center;justify-content:center;padding-top:20px}
.quote-text{left:270px;top:100px;width:660px;text-align:center;font-size:15.5px;line-height:26px;color:var(--white)}
.quote-name{left:0;top:193px;width:1200px;text-align:center;font-size:19px;font-weight:600}

/* footer */
.footer{left:0;top:2253px;width:1200px;height:341px;background:radial-gradient(ellipse 600px 200px at 50% 40%,#1c1818,transparent 80%),linear-gradient(180deg,#151213,#0e0c0c)}
.footer h3{position:absolute;top:70px;font-family:var(--sans);font-weight:600;font-size:19px;color:var(--white)}
.links{position:absolute;top:102px;list-style:none;font-size:12px;line-height:26px}
.links li{display:flex;align-items:center;gap:10px}
.links li::before{content:"";width:7px;height:7px;border:1.5px solid var(--white);border-radius:50%}
.social{top:104px;width:34px;height:34px;border:1.5px solid var(--red);border-radius:50%;display:flex;align-items:center;justify-content:center;font-size:9px;color:var(--red);font-weight:600}
.news-text{left:847px;top:101px;width:260px;font-size:12px;line-height:22px}
.news-input{left:847px;top:155px;width:254px;height:34px;border:1.5px solid var(--white);border-radius:17px;font-size:12px;display:flex;align-items:center;padding-left:14px;justify-content:space-between;padding-right:22px}
.rule{left:97px;top:284px;width:1004px;height:1px;background:var(--line)}
.copyright{left:0;top:301px;width:1200px;text-align:center;font-size:12px;color:var(--white)}
</style>
</head>
<body>
<div class="page">

  <header class="hero abs">
    <div class="hero-art abs" role="img" aria-label="Fantasy battle illustration: a fire-breathing dragon attacking armoured knights before a stone castle"></div>
    <div class="hero-shade abs"></div>
    <div class="brand abs">MARCUS<br>FELLWRIGHT</div>
    <nav class="nav abs">
      <a style="left:615px">Home</a>
      <a style="left:697px">Novels<span class="caret"></span></a>
      <a style="left:795px">World<span class="caret"></span></a>
      <a style="left:887px">Author<span class="caret"></span></a>
    </nav>
    <div class="search abs">
      <svg width="13" height="13" viewBox="0 0 13 13"><circle cx="5.5" cy="5.5" r="4" fill="none" stroke="#fff" stroke-width="2"/><line x1="8.5" y1="8.5" x2="12" y2="12" stroke="#fff" stroke-width="2.2"/></svg>
      <span>Search</span>
    </div>
    <h1 class="hero-title abs">THE LEGEND OF<br>VARNETH</h1>
  </header>

  <section class="novels abs">
    <h2 class="section-title abs">NOVELS</h2>
    <svg class="arrow abs" style="left:80px;top:294px" viewBox="0 0 26 30"><path d="M18 4 L7 15 L18 26" fill="none" stroke="#fff" stroke-width="5"/></svg>
    <div class="cover cover-1 abs" role="img" aria-label="Book cover of The Scarlet Blade, book one"></div>
    <div class="cover cover-2 abs" role="img" aria-label="Book cover of The Onyx Key, book two"></div>
    <div class="cover cover-3 abs" role="img" aria-label="Book cover of The Sacred Amulet, book three"></div>
    <svg class="arrow abs" style="left:1097px;top:294px" viewBox="0 0 26 30"><path d="M8 4 L19 15 L8 26" fill="none" stroke="#fff" stroke-width="5"/></svg>
  </section>

  <section class="world abs" role="img" aria-label="Dark background of twisted bare trees in amber light">
    <div class="feature abs" style="left:104px">
      <svg width="56" height="50" viewBox="0 0 56 50"><path d="M3 8 L19 3 L37 8 L53 3 L53 42 L37 47 L19 42 L3 47 Z M19 3 L19 42 M37 8 L37 47" fill="none" stroke="#fff" stroke-width="3.5" stroke-linejoin="round"/></svg>
    </div>
    <div class="feature-label abs" style="left:76px">Maps</div>
    <div class="feature abs" style="left:291px">
      <svg width="60" height="44" viewBox="0 0 60 44"><circle cx="30" cy="12" r="9" fill="#fff"/><circle cx="12" cy="17" r="6.5" fill="#fff"/><circle cx="48" cy="17" r="6.5" fill="#fff"/><path d="M15 44 C15 28 45 28 45 44 Z" fill="#fff"/><path d="M0 40 C0 28 14 26 18 30 C14 33 13 37 13 40 Z M60 40 C60 28 46 26 42 30 C46 33 47 37 47 40 Z" fill="#fff"/></svg>
    </div>
    <div class="feature-label abs" style="left:263px">Characters</div>
    <div class="feature abs" style="left:476px">
      <svg width="34" height="48" viewBox="0 0 34 48"><path d="M17 2 C8 2 2 9 2 17 C2 28 17 46 17 46 C17 46 32 28 32 17 C32 9 26 2 17 2 Z" fill="#fff"/><circle cx="17" cy="17" r="6" fill="#4a2614"/></svg>
    </div>
    <div class="feature-label abs" style="left:448px">Locations</div>
    <div class="feature abs" style="left:661px">
      <svg width="50" height="40" viewBox="0 0 50 40"><path d="M2 14 L11 14 L23 3 L23 37 L11 26 L2 26 Z" fill="#fff"/><path d="M30 13 Q35 20 30 27 M36 8 Q45 20 36 32 M42 3 Q55 20 42 37" fill="none" stroke="#fff" stroke-width="3.5" stroke-linecap="round"/></svg>
    </div>
    <div class="feature-label abs" style="left:633px">Artifacts</div>
    <h2 class="section-title abs">WORLD</h2>
    <p class="world-text abs">In this,View all the details of<br><em>“ The Legend of Varneth.”</em></p>
    <div class="btn-outline abs">View All Specials</div>
  </section>

  <section class="author abs">
    <div class="portrait abs" role="img" aria-label="Portrait photo of the author in a black shirt and red tie"></div>
    <h2 class="section-title abs">AUTHOR</h2>
    <div class="bio abs">
      <p>Weaned on the likes of The Warden of the Vales and Galaxy Reaches, Marcus took to writing fantasy adventure, it seems, almost as soon as he learned to read. By the time he hit grade school, he was writing 30-page stories in lieu of the two or three pages expected of all students on a monthly basis. When at age nine he read Dennis Vale's The Runestones of Merivane, his goal of becoming a fantasy novelist went from child's ambition to hopeless obsession.</p>
      <p>Yet writing was to be a hobby. Even his parents stressed the importance of a “safe” career path. So when the time came, Marcus accepted a scholarship and went off to college, where among his English, writing, and mythology courses, he studied computers, the health sciences, and worked hard to play football. What he really wanted to be was a quarterback.</p>
    </div>
    <div class="btn-red abs">Read More</div>
  </section>

  <section class="quote-band abs">
    <div class="quote-badge abs">
      <svg width="24" height="18" viewBox="0 0 24 18"><path d="M1 18 L1 9 Q1 2 9 0 L10 3 Q6 5 6 9 L10 9 L10 18 Z M14 18 L14 9 Q14 2 22 0 L23 3 Q19 5 19 9 L23 9 L23 18 Z" fill="var(--red)"/></svg>
    </div>
    <svg class="abs" style="left:72px;top:103px" width="22" height="32" viewBox="0 0 22 32"><path d="M17 3 L5 16 L17 29" fill="none" stroke="#fff" stroke-width="3"/></svg>
    <p class="quote-text abs">“ Sed cursus purus pharetra condimentum fermentum. Maecenas non libero id odio fring illa luctus. Pellen tesque habitant morbi trisertique senectus et netusw et malesuaada fames eugiat felis in enimsim. ”</p>
    <div class="quote-name abs">- Stella Deo</div>
    <svg class="abs" style="left:1104px;top:103px" width="22" height="32" viewBox="0 0 22 32"><path d="M5 3 L17 16 L5 29" fill="none" stroke="#fff" stroke-width="3"/></svg>
  </section>

  <footer class="footer abs">
    <h3 style="left:97px">Quick Links</h3>
    <ul class="links" style="left:104px">
      <li>Home</li><li>Novals</li><li>World</li><li>Author</li><li>Connect</li>
    </ul>
    <h3 style="left:320px">Other Links</h3>
    <ul class="links" style="left:326px">
      <li>Events</li><li>Q &amp; A</li><li>Art Gallery</li><li>Interviews</li><li>News</li>
    </ul>
    <h3 style="left:548px">Connect With Us On</h3>
    <div class="social abs" style="left:550px">Folio</div>
    <div class="social abs" style="left:596px">Chirp</div>
    <div class="social abs" style="left:642px">
      <svg width="15" height="11" viewBox="0 0 15 11"><rect x="0.75" y="0.75" width="13.5" height="9.5" fill="none" stroke="var(--red)" stroke-width="1.5"/><path d="M1 1 L7.5 6 L14 1" fill="none" stroke="var(--red)" stroke-width="1.5"/></svg>
    </div>
    <h3 style="left:847px">Newsletter Subscribe</h3>
    <p class="news-text abs">Hendrerit vulputate velit esse molestie soluta coaxc nsafg bxf esatv quat velillum nobis.</p>
    <div class="news-input abs">
      <span>Your Email Address</span>
      <svg width="16" height="12" viewBox="0 0 16 12"><rect x="0.75" y="0.75" width="14.5" height="10.5" fill="none" stroke="var(--red)" stroke-width="1.5"/><path d="M1 1 L8 6.5 L15 1" fill="none" stroke="var(--red)" stroke-width="1.5"/></svg>
    </div>
    <div class="rule abs"></div>
    <p class="copyright abs">Copyright © 2018. All Rights Reserved.</p>
  </footer>

</div>
</body>
</html>
```